Financial Advisor Resource Firm needs business card design

Need business card design for company in Omaha NE called Meridale Circle. We provide resources to financial advisors....workshop programs, retirement analysis, and insurance planning. I would like to see designs that use grays, greens, black, and white colors. The final design should communicate 'collaboration' and be simple yet attractive to financial planning clients. I will attached our logo and another picture of a puzzle piece coming together. I would like the incorporate the puzzle picture somehow, maybe on the back somehow, with color or just the gray scale....OR, the picture be the front of the card with 'Meridale' definition on it (see upload) and then company logo, employee name, title, address on the back (see ppt uploaded). The following disclosure needs to be included somewhere- Advisory services offered through Stonebrook Assets, LLC.
Updates

I uploaded a svg and ai file of the logo

Target Market(s)

Financial planning clients and financial advisors....so pretty diverse age range of about 40-70.

Industry/Entity Type

Financial Planning

Contact Information for Business Card

Tobias L. Fenwright, MBA
Founder/President
5287 E. Larkin Road
Suite 230
Omaha, NE 68190
Phone- (402) 555-0147
Cell- (402) 555-0183
Fax- (402) 555-0129
email- tobias@meridaleplan.example
web address- www.meridaleplan.example

Colors
1b1b1b
474747
d3d3d3
ffffff
9bcb3c
abd036

Requirements
Must have
• Must include logo provided, must be 2 sided, and must have disclosure...all of these items listed in project description

```html
<!DOCTYPE html>
<html lang="en">
<head>
<meta charset="utf-8">
<title>Meridale Circle — Business Card</title>
<link rel="stylesheet" href="https://fonts.googleapis.com/css2?family=Poppins:wght@300;400;600&display=swap">
<style>
  :root {
    --ink: #1b1b1b;
    --charcoal: #2b2b2b;
    --slate: #474747;
    --mist: #d3d3d3;
    --paper: #ffffff;
    --leaf: #9bcb3c;
    --lime: #abd036;
    --backdrop: #e9e9e7;
  }
  * { margin: 0; padding: 0; box-sizing: border-box; }
  html, body { width: 1200px; height: 862px; overflow: hidden; }
  body {
    background: var(--backdrop);
    font-family: "Poppins", Arial, sans-serif;
    position: relative;
  }
  .card {
    position: absolute;
    left: 240px;
    width: 720px;
    height: 410px;
    overflow: hidden;
    box-shadow: 0 6px 18px rgba(0,0,0,.18);
  }
  .card--front { top: 14px; background: var(--charcoal); }
  .card--back  { top: 438px; background: var(--paper); }

  .wordmark {
    position: absolute;
    display: flex;
    align-items: center;
    gap: 12px;
    font-weight: 600;
    letter-spacing: 2px;
    text-transform: uppercase;
  }
  .wordmark__dot {
    width: 14px; height: 14px; border-radius: 50%;
    background: var(--leaf);
  }
  .card--front .wordmark {
    left: 0; right: 0; top: 170px; justify-content: center;
    font-size: 40px; color: var(--paper);
  }
  .front-web {
    position: absolute; right: 120px; bottom: 72px;
    color: var(--paper); font-size: 15px; font-weight: 300; letter-spacing: .5px;
  }
  .front-web .accent { color: var(--leaf); }

  .back-art { position: absolute; inset: 0; }
  .card--back .wordmark {
    right: 40px; top: 52px; font-size: 24px; color: var(--ink);
  }
  .name-bar {
    position: absolute; left: 0; top: 120px; width: 10px; height: 30px;
    background: var(--leaf);
  }
  .holder { position: absolute; left: 40px; top: 118px; }
  .holder__name {
    color: var(--leaf); font-weight: 600; font-size: 19px;
    text-transform: uppercase; letter-spacing: .5px;
  }
  .holder__title { color: var(--slate); font-size: 14px; margin-top: 2px; }

  .contacts {
    position: absolute; left: 150px; top: 262px; list-style: none;
    color: var(--paper); font-size: 14px; font-weight: 300;
  }
  .contacts li { display: flex; align-items: center; gap: 10px; height: 25px; }
  .contacts .icon { width: 17px; height: 17px; flex: none; }
  .contacts .accent { color: var(--leaf); }

  .divider {
    position: absolute; left: 478px; top: 212px; width: 1px; height: 66px;
    background: var(--slate);
  }
  .office {
    position: absolute; left: 508px; top: 206px;
    color: var(--paper); font-size: 13px; line-height: 22px; font-weight: 300;
    font-style: normal;
  }
  .office__label { color: var(--leaf); font-weight: 400; }
  .disclosure {
    position: absolute; left: 508px; right: 30px; bottom: 26px;
    color: var(--mist); font-size: 10px; line-height: 14px; font-weight: 300;
  }
</style>
</head>
<body>

<section class="card card--front">
  <div class="wordmark"><span class="wordmark__dot"></span>Meridale Circle</div>
  <p class="front-web">www.<span class="accent">meridaleplan</span>.example</p>
</section>

<section class="card card--back">
  <svg class="back-art" viewBox="0 0 720 410" width="720" height="410" aria-hidden="true">
    <path d="M0,384 C38,226 300,146 720,134 L720,148 C300,158 42,238 0,398 Z" fill="var(--leaf)"/>
    <path d="M0,410 C40,250 300,170 720,160 L720,410 Z" fill="var(--charcoal)"/>
  </svg>

  <div class="wordmark"><span class="wordmark__dot"></span>Meridale Circle</div>

  <span class="name-bar"></span>
  <div class="holder">
    <p class="holder__name">Tobias L. Fenwright, MBA</p>
    <p class="holder__title">Founder / President</p>
  </div>

  <ul class="contacts">
    <li>
      <svg class="icon" viewBox="0 0 20 20"><circle cx="10" cy="10" r="10" fill="var(--leaf)"/><path d="M6.5 5.5l2 0 1 2.5-1.2 1a6 6 0 0 0 2.7 2.7l1-1.2 2.5 1 0 2a1 1 0 0 1-1 1A8 8 0 0 1 5.5 6.5a1 1 0 0 1 1-1z" fill="var(--paper)"/></svg>
      (402) 555-0147
    </li>
    <li>
      <svg class="icon" viewBox="0 0 20 20"><circle cx="10" cy="10" r="10" fill="var(--leaf)"/><rect x="7" y="4.5" width="6" height="11" rx="1" fill="var(--paper)"/><rect x="8" y="6" width="4" height="7" fill="var(--leaf)"/></svg>
      (402) 555-0183
    </li>
    <li>
      <svg class="icon" viewBox="0 0 20 20"><circle cx="10" cy="10" r="10" fill="var(--leaf)"/><rect x="7" y="5" width="6" height="3" fill="var(--paper)"/><rect x="5" y="8" width="10" height="5" rx="1" fill="var(--paper)"/><rect x="7" y="12" width="6" height="3" fill="var(--paper)"/></svg>
      (402) 555-0129
    </li>
    <li>
      <svg class="icon" viewBox="0 0 20 20"><circle cx="10" cy="10" r="10" fill="var(--leaf)"/><rect x="5" y="6.5" width="10" height="7" fill="var(--paper)"/><path d="M5 6.5l5 4 5-4" fill="none" stroke="var(--leaf)" stroke-width="1"/></svg>
      tobias@meridaleplan.example
    </li>
    <li>
      <svg class="icon" viewBox="0 0 20 20"><circle cx="10" cy="10" r="10" fill="var(--leaf)"/><circle cx="10" cy="10" r="5" fill="none" stroke="var(--paper)" stroke-width="1.2"/><ellipse cx="10" cy="10" rx="2.2" ry="5" fill="none" stroke="var(--paper)" stroke-width="1"/><path d="M5 10h10" stroke="var(--paper)" stroke-width="1"/></svg>
      <span>www.<span class="accent">meridaleplan</span>.example</span>
    </li>
  </ul>

  <span class="divider"></span>
  <address class="office">
    <p class="office__label">Meridaleplan</p>
    <p>5287 E. Larkin Road</p>
    <p>Suite 230</p>
  </address>

  <p class="disclosure">Advisory services offered through Stonebrook Assets, LLC.</p>
</section>

</body>
</html>
```